Employment Agency Website Design

We are working with an employment agency in California.

Some sites to use for content/competitors and inspiration:

https://www.pinecrestjobs.com/us/en
https://www.velmorusa.com
https://www.dravenworks.us
https://www.quillora.com/en
https://www.tomvalusa.com
https://www.fernstaffing.com

Thank you for taking the time to consider designing a website for us. We are web developers based in Stockton, CA, USA. Most of our projects go through the same process. Understanding this process may help you win a project with us. We custom-code all of our websites in-house. We don’t have any requirements as to what tools you use for your design, but we prefer Figma files. For any design that we label as four-stars, we send it to the client for review. The client picks the final design they want us to use. Once we complete this process, we will continue to show additional clients all the four-star sites and purchase them later. Your designs will have multiple chances to sell. For better chances of success, we ask that you follow these guidelines.

IMAGES:
If you use any images or icons in the design, we ask that you have a link to the asset so we can purchase the image/icon. Most of the designs we submit do not have the customer’s images on them unless they have some great images. Be creative; show us the feeling you are trying to portray with your image choices. Use any royalty-free site you choose. We subscribe to Adobe and mainly use their images, but we can purchase images outside of Adobe. PLEASE NOTE: we will not submit designs to clients with watermarks on the images.

FONTS:
We ask that you identify the fonts used in the design. This can be done in a message if you want. We typically use Google Fonts and Adobe Fonts.

CONTENT:
We're always open to different content and ideas. We often submit designs with stock images so the client can see our vision. We typically take pictures after the website launch to use their images with our vision. Lorem Ipsum is fine for paragraphs, but we ask that you write the headers in correct English. We want to be able to show the vision and identify the sections of the website.

INSPIRATION:
We typically add a couple of links in the brief of websites we like to help you get started in your design.

REVISIONS:
We do not often ask for revisions of the designs unless we see something in the design that may not appeal to the client. If there are slight changes that we want to make, we do that in the development process.

FEEDBACK:
We rarely give feedback on designs during the design process. We are working on many website projects and do not have the time to provide feedback. We usually respond if your request is well thought out and asks specific questions, but a note asking “feedback, please” usually goes unanswered.

```html
<!DOCTYPE html>
<html lang="en">
<head>
<meta charset="utf-8">
<title>Stridewell Talent — The Future Of Work</title>
<link href="https://fonts.googleapis.com/css2?family=Outfit:wght@400;500;600;700&family=Quicksand:wght@400;500;600;700&display=swap" rel="stylesheet">
<style>
:root{
  --red:#c8202f;
  --red-dark:#a51724;
  --ink:#1c1c1c;
  --muted:#555;
  --soft:#f3f0f0;
  --line:#e2e2e2;
  --white:#fff;
  --black:#0b0b0b;
  --head:'Outfit',sans-serif;
  --body:'Quicksand',sans-serif;
}
*{box-sizing:border-box;margin:0;padding:0}
html,body{width:1200px;height:4448px;overflow:hidden}
body{position:relative;font-family:var(--body);color:var(--ink);background:var(--white)}
.abs{position:absolute}
.btn{position:absolute;display:flex;align-items:center;justify-content:center;background:var(--red);color:#fff;font-family:var(--head);font-weight:600;font-size:13px;border-radius:4px}

/* hero */
.hero{left:0;top:0;width:1200px;height:751px;background:linear-gradient(100deg,#1b1613 0%,#3a2e26 35%,#5b6d80 65%,#8aa0b3 100%)}
.brand-tab{left:110px;top:0;width:182px;height:185px;background:#fff;clip-path:polygon(0 0,100% 0,100% 82%,50% 100%,0 82%);display:flex;flex-direction:column;align-items:center;justify-content:center;gap:8px}
.brand-dot{width:44px;height:44px;border-radius:50%;background:var(--red)}
.brand-name{font-family:var(--body);font-weight:700;font-size:18px;color:var(--ink)}
.nav{top:36px;left:0;width:1200px;height:24px;font-size:14px;font-weight:600;color:#fff}
.nav a{position:absolute;color:#fff;text-decoration:none}
.nav a.active::after{content:"";position:absolute;left:0;right:0;bottom:-10px;height:2px;background:var(--red)}
.hero-welcome{left:110px;top:264px;color:#fff;font-family:var(--head);font-size:22px;font-weight:500}
.hero-title{left:110px;top:295px;color:#fff;font-family:var(--head);font-size:62px;font-weight:600;letter-spacing:.5px}
.hero-sub{left:110px;top:385px;color:#fff;font-family:var(--head);font-size:25px;font-weight:400}

/* search */
.search-card{left:102px;top:696px;width:996px;height:147px;background:#fff;border-radius:22px;box-shadow:0 6px 20px rgba(0,0,0,.12);border:1px solid #eee}
.field{top:50px;height:47px;background:#f1f1f1;display:flex;align-items:center;gap:16px;padding-left:20px;font-size:13px;color:#444}

/* tabs */
.tab{position:absolute;top:946px;height:40px;border:1px solid #cfcfcf;border-radius:4px;font-size:13px;color:#555;display:flex;align-items:center;justify-content:center;background:#f7f7f7}
.tab.on{background:var(--red);color:#fff;border-color:var(--red);font-weight:600}

/* categories */
.cat{position:absolute;width:317px;height:58px;background:#fff;box-shadow:0 2px 8px rgba(0,0,0,.12);display:flex;align-items:center;padding:0 12px 0 14px;font-size:14px;color:#333}
.cat .ic{width:28px;height:28px;margin-right:18px;flex:none}
.cat .lbl{flex:1}
.cat.on{background:var(--red);color:#fff}

/* sections */
.band{left:0;width:1200px;background:var(--soft)}
.photo{position:absolute}
.h2{font-family:var(--head);font-weight:500;font-size:42px;line-height:1.22;color:var(--ink)}
.ticks li{position:absolute;list-style:none;display:flex;align-items:center;gap:18px;font-size:14.5px;color:#444;white-space:nowrap}
.career-card{position:absolute;top:2193px;width:316px;height:366px;border-radius:10px;overflow:hidden}
.career-card span{position:absolute;left:32px;bottom:28px;color:#fff;font-family:var(--head);font-weight:500;font-size:24px}
.circle-arrow{position:absolute;width:30px;height:30px;border-radius:50%;background:#fff;box-shadow:0 1px 5px rgba(0,0,0,.25);display:flex;align-items:center;justify-content:center}

/* testimonials */
.t-dots i{display:inline-block;height:4px;width:18px;background:#ccc;margin-right:5px}
.t-dots i.on{width:30px;background:var(--red)}

/* footer */
.footer{left:0;top:3862px;width:1200px;height:586px;background:var(--black)}
.cta{left:110px;top:3750px;width:978px;height:244px;background:var(--red);border-radius:24px;text-align:center;color:#fff}
.f-head{position:absolute;color:#fff;font-family:var(--head);font-weight:500;font-size:17px}
.f-link{position:absolute;color:#ddd;font-size:12.5px}
.f-div{position:absolute;top:4101px;width:2px;height:241px;background:var(--red)}
.social{position:absolute;top:4280px;width:19px;height:19px;border-radius:3px}
</style>
</head>
<body>

<!-- Hero -->
<section class="abs hero" role="img" aria-label="Two smiling colleagues reviewing paperwork at a laptop in a bright office"></section>
<div class="abs brand-tab"><div class="brand-dot"></div><div class="brand-name">Stridewell Talent</div></div>
<nav class="abs nav">
  <a class="active" style="left:413px">Home</a>
  <a style="left:489px">Find Jobs</a>
  <a style="left:590px">How To Apply</a>
  <a style="left:725px">View All Jobs</a>
  <a style="left:858px">Resources</a>
</nav>
<div class="btn" style="left:960px;top:31px;width:126px;height:41px">Contact US</div>
<div class="abs hero-welcome">Welcome To</div>
<h1 class="abs hero-title">Stridewell Talent</h1>
<div class="abs hero-sub">The Future Of Work</div>
<div class="btn" style="left:114px;top:452px;width:128px;height:40px">Get Started</div>

<!-- Search -->
<div class="abs search-card">
  <div class="abs field" style="left:31px;width:366px">
    <svg width="16" height="16" viewBox="0 0 16 16"><circle cx="7" cy="7" r="5" fill="none" stroke="#222" stroke-width="1.8"/><path d="M11 11l4 4" stroke="#222" stroke-width="1.8"/></svg>
    job titles,skills,or keywords
  </div>
  <div class="abs field" style="left:404px;width:366px">
    <svg width="14" height="18" viewBox="0 0 14 18"><path d="M7 1a6 6 0 0 1 6 6c0 4-6 10-6 10S1 11 1 7a6 6 0 0 1 6-6z" fill="none" stroke="#222" stroke-width="1.8"/><circle cx="7" cy="7" r="2" fill="#222"/></svg>
    City,state,or Zip Code
  </div>
  <div class="btn" style="left:798px;top:52px;width:148px;height:41px">Search jobs</div>
</div>

<!-- Tabs -->
<div class="tab on" style="left:271px;width:159px">Jobs by Industry</div>
<div class="tab" style="left:435px;width:161px">Jobs by State</div>
<div class="tab" style="left:603px;width:159px">Jobs by Type</div>
<div class="tab" style="left:768px;width:225px">Jobs by Featured Companies</div>

<!-- Categories -->
<svg width="0" height="0" style="position:absolute">
  <defs>
    <symbol id="arrow" viewBox="0 0 18 14"><path d="M1 7h15M10 1l6 6-6 6" fill="none" stroke="currentColor" stroke-width="1.8"/></symbol>
    <symbol id="ico" viewBox="0 0 28 28"><rect x="4" y="4" width="20" height="20" rx="4" fill="none" stroke="currentColor" stroke-width="1.6"/><path d="M9 14h10M14 9v10" stroke="currentColor" stroke-width="1.6"/></symbol>
    <symbol id="tick" viewBox="0 0 20 18"><path d="M2 9l6 6L18 2" fill="none" stroke="#111" stroke-width="2.4"/></symbol>
  </defs>
</svg>
<div class="cat" style="left:110px;top:1050px"><svg class="ic"><use href="#ico"/></svg><span class="lbl">Accounting &amp; Finance</span><svg width="18" height="14"><use href="#arrow"/></svg></div>
<div class="cat" style="left:439px;top:1050px"><svg class="ic"><use href="#ico"/></svg><span class="lbl">Hospitality</span><svg width="18" height="14"><use href="#arrow"/></svg></div>
<div class="cat" style="left:765px;top:1050px"><svg class="ic"><use href="#ico"/></svg><span class="lbl">Bpo</span><svg width="18" height="14"><use href="#arrow"/></svg></div>
<div class="cat" style="left:110px;top:1115px;font-size:13px"><svg class="ic"><use href="#ico"/></svg><span class="lbl">Office, Clerical, &amp; Administrative</span><svg width="18" height="14"><use href="#arrow"/></svg></div>
<div class="cat on" style="left:439px;top:1115px"><svg class="ic"><use href="#ico"/></svg><span class="lbl">Human Resources</span><svg width="18" height="14"><use href="#arrow"/></svg></div>
<div class="cat" style="left:765px;top:1115px"><svg class="ic"><use href="#ico"/></svg><span class="lbl">Industrial &amp; Manufacturing</span><svg width="18" height="14"><use href="#arrow"/></svg></div>
<div class="cat" style="left:110px;top:1184px"><svg class="ic"><use href="#ico"/></svg><span class="lbl">Medical &amp; Science</span><svg width="18" height="14"><use href="#arrow"/></svg></div>
<div class="cat" style="left:439px;top:1184px"><svg class="ic"><use href="#ico"/></svg><span class="lbl">Retail</span><svg width="18" height="14"><use href="#arrow"/></svg></div>
<div class="cat" style="left:765px;top:1184px"><svg class="ic"><use href="#ico"/></svg><span class="lbl">Transportation</span><svg width="18" height="14"><use href="#arrow"/></svg></div>
<div class="cat" style="left:110px;top:1253px"><svg class="ic"><use href="#ico"/></svg><span class="lbl">Warehousing</span><svg width="18" height="14"><use href="#arrow"/></svg></div>
<div class="cat" style="left:439px;top:1253px"><svg class="ic"><use href="#ico"/></svg><span class="lbl">Creative &amp; Marketing</span><svg width="18" height="14"><use href="#arrow"/></svg></div>
<div class="cat" style="left:765px;top:1253px"><svg class="ic"><use href="#ico"/></svg><span class="lbl">Engineering &amp; Technology</span><svg width="18" height="14"><use href="#arrow"/></svg></div>

<!-- Consulting -->
<section class="abs band" style="top:1402px;height:589px"></section>
<div class="photo" style="left:110px;top:1459px;width:470px;height:470px;background:linear-gradient(160deg,#e9eaea,#b9bec2 55%,#2f3338)" role="img" aria-label="Three consultants meeting around a laptop in a modern lounge"></div>
<h2 class="abs h2" style="left:641px;top:1472px">Consulting Solutions To<br>Drive Business Impact</h2>
<ul class="ticks">
  <li style="left:641px;top:1618px"><svg width="20" height="18"><use href="#tick"/></svg>Lorem ipsum dolor sit amet, consectetur adipiscing elit</li>
  <li style="left:641px;top:1670px"><svg width="20" height="18"><use href="#tick"/></svg>&nbsp;sed do eiusmod tempor incididunt ut labore et dolore</li>
  <li style="left:641px;top:1720px"><svg width="20" height="18"><use href="#tick"/></svg>Ut enim ad minim veniam quis nostrud exercitation</li>
  <li style="left:641px;top:1774px"><svg width="20" height="18"><use href="#tick"/></svg>Excepteur sint occaecat cupidatat non proident, sunt</li>
</ul>
<div class="btn" style="left:641px;top:1837px;width:186px;height:40px">Find Your Consulting</div>

<!-- Career forward -->
<h2 class="abs h2" style="left:0;width:1186px;top:2068px;text-align:center;font-size:40px">Move Your Career Forward</h2>
<div class="career-card" style="left:110px;background:linear-gradient(180deg,#8b97ad,#4a5468 60%,#1b1c22)" role="img" aria-label="Hands typing on a laptop showing a job search screen"><span>Find a job that fits you</span></div>
<div class="career-card" style="left:442px;background:linear-gradient(180deg,#d7d7d5,#a89a86 60%,#2a2622)" role="img" aria-label="Young woman writing notes beside a laptop"><span>Build your resume</span></div>
<div class="career-card" style="left:772px;background:linear-gradient(180deg,#a9a7a2,#6d5d4c 60%,#1f1a16)" role="img" aria-label="Candidates seated in a row waiting for interviews"><span>Today’s in demand jobs</span></div>
<div class="circle-arrow" style="left:32px;top:2394px"><svg width="14" height="12" viewBox="0 0 18 14"><path d="M17 7H2M8 1L2 7l6 6" fill="none" stroke="#c8202f" stroke-width="1.8"/></svg></div>
<div class="circle-arrow" style="left:1128px;top:2394px"><svg width="14" height="12" viewBox="0 0 18 14" style="color:#c8202f"><use href="#arrow"/></svg></div>

<!-- Career move -->
<section class="abs band" style="top:2654px;height:587px"></section>
<h2 class="abs h2" style="left:110px;top:2732px">Make the career move<br>you want</h2>
<ul class="ticks">
  <li style="left:110px;top:2868px"><svg width="20" height="18"><use href="#tick"/></svg>Lorem ipsum dolor sit amet, consectetur adipiscing elit</li>
  <li style="left:110px;top:2920px"><svg width="20" height="18"><use href="#tick"/></svg>&nbsp;sed do eiusmod tempor incididunt ut labore et dolore</li>
  <li style="left:110px;top:2971px"><svg width="20" height="18"><use href="#tick"/></svg>Ut enim ad minim veniam quis nostrud exercitation</li>
  <li style="left:110px;top:3023px"><svg width="20" height="18"><use href="#tick"/></svg>Excepteur sint occaecat cupidatat non proident, sunt</li>
</ul>
<div class="btn" style="left:110px;top:3087px;width:186px;height:40px">Find Your Consulting</div>
<div class="photo" style="left:616px;top:2709px;width:470px;height:470px;background:linear-gradient(150deg,#eef0f0,#c9ccd0 50%,#2b3446)" role="img" aria-label="Smiling professional woman holding a tablet"></div>

<!-- Testimonials -->
<h2 class="abs h2" style="left:630px;top:3322px">Our Testimonials</h2>
<div class="abs" style="left:154px;top:3360px;width:48px;height:102px;border-radius:24px;background:#111"></div>
<div class="abs" style="left:218px;top:3370px;width:43px;height:294px;border-radius:22px;background:var(--red)"></div>
<div class="abs" style="left:203px;top:3390px;width:250px;height:250px;border-radius:50%;background:radial-gradient(circle at 50% 45%,#e9e3dc,#9ac5cf)" role="img" aria-label="Portrait of a smiling client with crossed arms"></div>
<div class="abs" style="left:616px;top:3418px;font-family:var(--head);font-size:44px;font-weight:700;line-height:1">“</div>
<div class="abs" style="left:649px;top:3448px;font-size:16px;font-weight:600">Renata</div>
<div class="abs" style="left:722px;top:3450px;color:#e8b923;font-size:13px;letter-spacing:1px">★★★★★</div>
<div class="abs" style="left:649px;top:3476px;color:var(--red);font-size:12px;font-weight:600">Student</div>
<p class="abs" style="left:649px;top:3512px;width:450px;font-size:12.5px;line-height:24px;color:#555">Lorem ipsum dolor sit amet, consectetur adipiscing elit, sed do eiusmod tempor incididunt ut labore et dolore magna aliqua. Ut enim ad minim veniam, quis nostrud exercitation ullamco laboris nisi ut aliquip ex ea commodo consequat.</p>
<div class="abs t-dots" style="left:649px;top:3622px"><i class="on"></i><i></i><i></i><i></i></div>
<div class="abs" style="left:870px;top:3610px;font-family:var(--head);font-size:44px;font-weight:700;line-height:1">”</div>

<!-- Footer -->
<footer class="abs footer"></footer>
<div class="abs cta">
  <h2 style="font-family:var(--head);font-weight:500;font-size:42px;margin-top:50px">Discover your best self. Job included</h2>
  <p style="font-size:11.5px;line-height:24px;width:640px;margin:8px auto 0">Lorem ipsum dolor sit amet, consectetur adipiscing elit, sed do eiusmod tempor incididunt ut labore et dolore magna aliqua. Ut enim ad minim veniam, quis nostrud exercitation ullamco laboris nisi ut aliquip .</p>
</div>
<div class="abs" style="left:539px;top:3922px;width:122px;height:41px;background:#fff;border-radius:4px;display:flex;align-items:center;justify-content:center;font-family:var(--head);font-weight:600;font-size:13px">Contact Us</div>

<div class="abs" style="left:110px;top:4110px;width:220px;display:flex;flex-direction:column;align-items:center;gap:10px">
  <div style="width:64px;height:64px;border-radius:50%;background:var(--red)"></div>
  <div style="color:#fff;font-weight:700;font-size:22px">Stridewell Talent</div>
</div>
<div class="abs" style="left:116px;top:4258px;width:274px;height:43px;background:#fff;border-radius:3px;display:flex;align-items:center;padding-left:16px;font-size:12px;color:#444">Enter Email Address</div>
<div class="btn" style="left:114px;top:4316px;width:104px;height:30px;font-size:12px">Subscribe</div>

<div class="f-head" style="left:489px;top:4100px">Quick Links</div>
<div class="f-link" style="left:489px;top:4141px">Home</div>
<div class="f-link" style="left:489px;top:4174px">Find Jobs</div>
<div class="f-link" style="left:489px;top:4208px">How To Apply</div>
<div class="f-link" style="left:489px;top:4241px">View All Jobs</div>
<div class="f-link" style="left:489px;top:4274px">Resources</div>
<div class="f-div" style="left:640px"></div>
<div class="f-head" style="left:694px;top:4100px">Other Links</div>
<div class="f-link" style="left:694px;top:4141px">Privacy Policy</div>
<div class="f-link" style="left:694px;top:4174px">Terms &amp; Cpnditions</div>
<div class="f-head" style="left:694px;top:4230px">Follow Us</div>
<div class="social" style="left:698px;background:#2d6cdf"></div>
<div class="social" style="left:722px;background:#fff"></div>
<div class="social" style="left:748px;background:#d6336c"></div>
<div class="social" style="left:772px;background:#b23ac6"></div>
<div class="social" style="left:797px;background:#e0222a"></div>
<div class="f-div" style="left:871px"></div>
<div class="f-head" style="left:908px;top:4100px">Contact Info</div>
<svg class="abs" style="left:908px;top:4140px" width="14" height="20" viewBox="0 0 14 20"><path d="M7 1a6 6 0 0 1 6 6c0 5-6 12-6 12S1 12 1 7a6 6 0 0 1 6-6z" fill="#fff"/><circle cx="7" cy="7" r="2.3" fill="#000"/></svg>
<div class="f-link" style="left:943px;top:4141px">Lorem Ipsum,Usa -4379</div>
<svg class="abs" style="left:908px;top:4198px" width="16" height="16" viewBox="0 0 16 16"><path d="M3 1l3 3-2 2c1 2 3 4 5 5l2-2 3 3-2 3C7 15 1 9 1 3z" fill="#fff"/></svg>
<div class="f-link" style="left:943px;top:4199px">+1 888 888 8888</div>
<svg class="abs" style="left:906px;top:4255px" width="20" height="14" viewBox="0 0 20 14"><rect x="1" y="1" width="18" height="12" fill="none" stroke="#fff" stroke-width="1.5"/><path d="M1 1l9 7 9-7" fill="none" stroke="#fff" stroke-width="1.5"/></svg>
<div class="f-link" style="left:943px;top:4253px">info@stridewelltalent.com</div>

<div class="abs" style="left:110px;top:4403px;width:978px;height:1px;background:#555"></div>
<div class="abs" style="left:0;width:1200px;top:4418px;text-align:center;color:#ddd;font-size:12px">Copyright © 2024 Stridewell Talent. All rights reserved.</div>

</body>
</html>
```